Marine Services Letterhead design

We need a letterhead design for an Australian owned company in Victoria named K+T Harbour Works Pty Ltd. We provide linesmen and launches to assist the large ships that come into port.
Our colour is orange.
The final design should have a strong nautical theme and communicate safety and reliability.
I would like to use the letter head on invoices so it should print to pdf well.

Target Market(s)

Owners and representatives of shipping companies. It is not for general public

Industry/Entity Type

Nautical

Requirements
Must have
• A shipping theme, not overly complicated, featuring safety orange colours but not all orange of course.
The letterhead should just sit at the top of the page so I can use for invoices.
Nice to have
• Something elegant and stylish
Should not have
• cartoons or pop art

```html
<!DOCTYPE html>
<html lang="en">
<head>
<meta charset="utf-8">
<title>K+T Harbour Works Pty Ltd – Letterhead</title>
<link rel="stylesheet" href="https://fonts.googleapis.com/css2?family=Source+Sans+3:wght@400;600&display=swap">
<style>
  :root {
    --page: #ffffff;
    --surround: #ffffff;
    --band: #b0682a;
    --accent: #b97a3b;
    --ink: #4a4a4a;
    --rule: #1a1a1a;
    --frame: #6a6a6a;
    --panel: #f2f2f2;
    --divider: #8a8a8a;
    --watermark: #e3e3e3;
  }
  * { margin: 0; padding: 0; box-sizing: border-box; }
  html, body {
    width: 961px; height: 1200px; overflow: hidden;
    background: var(--surround);
  }
  body { font-family: "Source Sans 3", "Myriad Pro", sans-serif; }
  .letterhead {
    position: relative; width: 961px; height: 1200px;
    background: var(--page);
    border: 1px solid var(--frame);
    overflow: hidden;
  }
  .side-band {
    position: absolute; left: 0; top: 0; bottom: 0;
    width: 118px; background: var(--band);
  }
  .side-rule {
    position: absolute; left: 122px; top: 0; bottom: 0;
    width: 2px; background: var(--rule);
  }
  .brand-panel {
    position: absolute; left: 45px; top: 33px;
    width: 275px; height: 228px;
    background: var(--panel);
  }
  .brand-mark {
    position: absolute; left: 22px; top: 26px;
    width: 253px; height: 170px;
    background: var(--page);
    box-shadow: 6px 8px 12px rgba(0,0,0,0.35);
    display: flex; align-items: center; justify-content: center;
    gap: 10px; padding: 0 14px;
  }
  .brand-dot {
    flex: none; width: 16px; height: 16px; border-radius: 50%;
    background: var(--band);
  }
  .brand-name {
    font-weight: 600; font-size: 22px; line-height: 1.15;
    color: var(--band);
  }
  .watermark {
    position: absolute; right: 14px; top: 990px;
    width: 230px; height: 200px;
    display: flex; flex-direction: column; align-items: center; justify-content: center;
    gap: 10px;
  }
  .watermark-dot {
    width: 46px; height: 46px; border-radius: 50%;
    background: var(--watermark);
  }
  .watermark-name {
    font-weight: 600; font-size: 44px; line-height: 1.05;
    color: var(--watermark); text-align: center;
  }
  .footer {
    position: absolute; left: 143px; top: 1124px;
    display: flex; align-items: stretch;
  }
  .footer-identity { padding-right: 28px; }
  .company-name {
    font-weight: 600; font-size: 22px; color: var(--accent);
    line-height: 1;
  }
  .address {
    margin-top: 14px; font-size: 17px; color: var(--ink);
    display: flex; align-items: center; gap: 6px;
  }
  .footer-divider { width: 1px; background: var(--divider); }
  .footer-contact { padding-left: 24px; font-size: 19px; color: var(--ink); }
  .phone { display: flex; align-items: center; gap: 4px; line-height: 1; }
  .abn { margin-top: 12px; line-height: 1; }
  .icon { flex: none; }
</style>
</head>
<body>
  <main class="letterhead">
    <div class="side-band"></div>
    <div class="side-rule"></div>

    <div class="brand-panel">
      <div class="brand-mark">
        <span class="brand-dot"></span>
        <span class="brand-name">K+T Harbour Works</span>
      </div>
    </div>

    <div class="watermark" aria-hidden="true">
      <span class="watermark-dot"></span>
      <span class="watermark-name">K+T Harbour Works</span>
    </div>

    <footer class="footer">
      <div class="footer-identity">
        <p class="company-name">K+T Harbour Works Pty Ltd</p>
        <p class="address">
          <svg class="icon" width="12" height="18" viewBox="0 0 12 18" aria-hidden="true">
            <path d="M6 0C2.7 0 0 2.6 0 5.9 0 10.3 6 18 6 18s6-7.7 6-12.1C12 2.6 9.3 0 6 0zm0 8.3A2.4 2.4 0 1 1 6 3.5a2.4 2.4 0 0 1 0 4.8z" fill="var(--band)"/>
          </svg>
          PO Box 214 Seacliff 3990
        </p>
      </div>
      <div class="footer-divider"></div>
      <div class="footer-contact">
        <p class="phone">
          <svg class="icon" width="20" height="20" viewBox="0 0 20 20" aria-hidden="true">
            <circle cx="10" cy="10" r="8.5" fill="none" stroke="var(--accent)" stroke-width="1.6"/>
            <path d="M7.2 5.2l2 2.3-1.1 1.3c.6 1.3 1.5 2.3 2.8 3l1.3-1.1 2.2 1.9-1.2 1.8c-3.6-.4-6.6-3.4-7-7z" fill="var(--accent)"/>
          </svg>
          1300 418 276
        </p>
        <p class="abn">ABN: 48203615790</p>
      </div>
    </footer>
  </main>
</body>
</html>
```